Larkmoor Home Works Sales Flyer

We want a sales flyer that outlines our companies strengths with Kitchen & Bath Remodeling. We would like highlight those aspects while also showcasing our ability to do decks and home additions. We want financing packages to be a big part of the flyer.

Target Market(s)

Residential Customers

Requirements
Must have
• Financing options
Highlight Kitchen & bath remodeling
Less subtle is our decks and home additions
Nice to have
• Keep within our logo colors-we are looking for informative flyers that leave homeowners eager to call us after a meeting

```html
<!DOCTYPE html>
<html lang="en">
<head>
<meta charset="utf-8">
<title>Larkmoor Home Works – Remodeling Flyer</title>
<link href="https://fonts.googleapis.com/css2?family=Source+Sans+3:wght@400;600;700&display=swap" rel="stylesheet">
<style>
:root{
  --sky:#00b2f0;
  --blue:#0a7fd6;
  --navy:#1b3aa6;
  --navy-dark:#1a2e8f;
  --orange:#f05a28;
  --orange-soft:rgba(240,110,60,.88);
  --ink:#3d3d3d;
  --bullet:#1b3aa6;
  --panel:#f4f4f4;
  --white:#ffffff;
}
*{margin:0;padding:0;box-sizing:border-box}
html,body{width:933px;height:1200px;overflow:hidden}
body{font-family:"Source Sans 3",Arial,sans-serif;color:var(--ink);background:var(--white)}
.flyer{position:relative;width:933px;height:1200px;overflow:hidden}

.masthead{position:absolute;left:0;top:0;width:933px;height:180px;
  background:linear-gradient(180deg,var(--sky) 0%,var(--blue) 100%)}
.brand{position:absolute;left:80px;top:98px;width:360px;color:var(--white);white-space:nowrap;
  font-weight:600;font-size:27px;letter-spacing:1px;line-height:32px;display:flex;align-items:center;justify-content:center;gap:10px}
.brand-dot{width:12px;height:12px;border-radius:50%;background:var(--white);flex:none}
.estimate{position:absolute;right:54px;top:50px;width:230px;text-align:center;color:var(--white)}
.estimate .line{font-size:20px;line-height:28px}
.estimate .line b{font-weight:700}
.estimate .phone{font-size:27px;font-weight:700;line-height:34px;display:flex;align-items:center;justify-content:center;gap:8px}
.phone-icon{width:13px;height:13px;border-radius:50%;background:#e2473b;display:inline-block}

.hero{position:absolute;left:0;top:180px;width:933px;height:368px;overflow:hidden}
.hero-living{position:absolute;left:0;top:0;width:540px;height:368px;
  background:linear-gradient(160deg,#c9c2b8 0%,#8d8579 45%,#5d5a58 100%)}
.hero-bathroom{position:absolute;left:445px;top:0;width:488px;height:368px;
  clip-path:polygon(88px 0,488px 0,488px 368px,0 368px);
  background:linear-gradient(150deg,#8f959d 0%,#b7bbc0 40%,#d9d7d3 75%,#ece9e4 100%)}
.hero-tagline{position:absolute;left:0;top:125px;width:484px;height:151px;background:var(--orange-soft);
  padding:16px 0 0 69px;color:var(--white);font-size:34.5px;line-height:35.5px;white-space:nowrap}
.hero-tagline b{font-weight:700}
.hero-headline{position:absolute;left:72px;top:290px;color:var(--white);font-weight:700;font-size:35.5px;
  line-height:33px;text-shadow:1px 2px 3px rgba(0,0,0,.55);letter-spacing:-.2px;white-space:nowrap}

.financing{position:absolute;left:0;top:548px;width:933px;height:29px;background:var(--orange);
  color:var(--white);font-weight:700;font-size:20px;line-height:29px;text-align:center}

.service{position:absolute;background:linear-gradient(180deg,#fff 0%,var(--panel) 100%)}
.service h2{position:absolute;color:var(--orange);font-weight:600;font-size:17.5px;letter-spacing:.2px;white-space:nowrap}
.service .intro{position:absolute;font-size:14.5px;line-height:15px}
.service ul{position:absolute;list-style:none;font-size:14.5px}
.service li{position:relative;padding-left:12px;white-space:nowrap}
.service li::before{content:"";position:absolute;left:0;top:7px;width:4px;height:4px;background:var(--bullet)}
.icon{position:absolute}
.photo{position:absolute}

.service-kitchen{left:0;top:577px;width:466px;height:257px}
.service-bathroom{left:466px;top:577px;width:467px;height:257px}
.service-additions{left:0;top:834px;width:466px;height:296px;background:#fafafa}
.service-decks{left:466px;top:834px;width:467px;height:296px;background:#fafafa}

.footer{position:absolute;left:0;top:1130px;width:933px;height:70px;
  background:linear-gradient(90deg,var(--navy) 0%,var(--navy-dark) 100%);border-top:3px solid var(--blue)}
.footer .contact{position:absolute;top:24px;color:var(--white);font-size:16px;display:flex;align-items:center;gap:14px;white-space:nowrap}
</style>
</head>
<body>
<div class="flyer">

  <header class="masthead">
    <div class="brand"><span class="brand-dot"></span>LARKMOOR HOME WORKS</div>
    <div class="estimate">
      <div class="line">CALL TODAY FOR YOUR</div>
      <div class="line"><b>FREE</b> ESTIMATE</div>
      <div class="phone"><span class="phone-icon"></span>515-555-0148</div>
    </div>
  </header>

  <section class="hero">
    <div class="hero-living" role="img" aria-label="Bright open-plan living room with stone fireplace wall and kitchen island"></div>
    <div class="hero-bathroom" role="img" aria-label="Remodeled bathroom with marble tile glass shower and white vanity"></div>
    <div class="hero-tagline">Ready for<br>a Beautiful and Functional<br><b>Kitchen</b> or <b>Bathroom</b>?</div>
    <h1 class="hero-headline">WORK WITH A TOP-RATED LOCAL REMODELING<br>COMPANY IN ANKENY, IA</h1>
  </section>

  <div class="financing">$ FINANCING OPTIONS AVAILABLE $</div>

  <section class="service service-kitchen">
    <svg class="icon" style="left:38px;top:22px" width="48" height="48" viewBox="0 0 48 48" fill="none" stroke="#1b3aa6" stroke-width="2">
      <rect x="2" y="22" width="44" height="24"/><line x1="2" y1="27" x2="46" y2="27"/>
      <rect x="6" y="31" width="14" height="11"/><rect x="26" y="31" width="16" height="11"/>
      <line x1="6" y1="36" x2="20" y2="36"/><circle cx="12" cy="14" r="4"/><line x1="6" y1="4" x2="6" y2="20"/>
      <path d="M30 8h12M36 4v4"/>
    </svg>
    <h2 style="left:104px;top:18px">KITCHEN REMODELING</h2>
    <p class="intro" style="left:105px;top:48px;width:345px">Whatever your vision is for your new kitchen, our crew can help you bring it to life. You can trust us for:</p>
    <ul style="left:105px;top:92px;line-height:16.4px">
      <li>Open concept design services</li>
      <li>Kitchen cabinet installation services</li>
      <li>Kitchen countertop installation services</li>
      <li>Tile installation services</li>
      <li>Lighting installation services</li>
      <li>Plumbing upgrade services</li>
      <li>Electrical upgrade services</li>
      <li>Drywall services</li>
      <li>Painting services</li>
    </ul>
  </section>

  <section class="service service-bathroom">
    <svg class="icon" style="left:26px;top:22px" width="48" height="48" viewBox="0 0 48 48" fill="none" stroke="#1b3aa6" stroke-width="2">
      <circle cx="25" cy="10" r="8"/><line x1="21" y1="13" x2="29" y2="7"/>
      <rect x="3" y="26" width="42" height="20"/><line x1="3" y1="31" x2="45" y2="31"/>
      <line x1="24" y1="31" x2="24" y2="46"/><path d="M16 26c0-4 4-6 8-6s8 2 8 6"/><rect x="6" y="18" width="4" height="8"/>
    </svg>
    <h2 style="left:92px;top:18px">BATHROOM REMODELING</h2>
    <p class="intro" style="left:93px;top:47px;width:335px">When you hire us for your bathroom remodeling project, the possibilities are endless. Our experienced and talented team can:</p>
    <ul style="left:93px;top:107px;line-height:15px">
      <li style="margin-bottom:3px">Install a custom tile shower</li>
      <li style="margin-bottom:3px">Build a new vanity</li>
      <li style="margin-bottom:3px">Install flooring and tile</li>
      <li style="margin-bottom:3px">Replace your plumbing and<br>light fixtures</li>
      <li style="margin-bottom:3px">Jetted tubs</li>
      <li>Steam showers</li>
    </ul>
    <div class="photo" role="img" aria-label="Marble-tiled bathroom with glass shower and double vanity"
      style="left:290px;top:101px;width:177px;height:156px;background:linear-gradient(150deg,#a9aeb5 0%,#d6d6d4 55%,#efece7 100%)"></div>
  </section>

  <section class="service service-additions">
    <svg class="icon" style="left:38px;top:18px" width="48" height="48" viewBox="0 0 48 48" fill="none" stroke="#1b3aa6" stroke-width="2">
      <path d="M2 34h8v-8h8v-8h8V2h20v44H2z"/><path d="M10 26V6h8v12M18 18V4M26 2v24"/><path d="M34 2v10M40 2v10"/>
    </svg>
    <h2 style="left:108px;top:16px">HOME ADDITIONS</h2>
    <p class="intro" style="left:109px;top:46px;width:345px">No matter what kind of space you need, our team will bring your vision to life. You can hire us if you need a:</p>
    <ul style="left:109px;top:92px;line-height:17.8px">
      <li>Bathroom addition</li>
      <li>Bedroom addition</li>
      <li>Garage addition</li>
      <li>Basement addition</li>
      <li>Guest room addition</li>
      <li>Living room addition</li>
      <li>Sunroom addition</li>
    </ul>
    <div class="photo" role="img" aria-label="Bright bedroom with upholstered bed and wood floors"
      style="left:270px;top:116px;width:196px;height:180px;background:linear-gradient(170deg,#dcd8d0 0%,#c7c0b3 55%,#b39d80 100%)"></div>
  </section>

  <section class="service service-decks">
    <svg class="icon" style="left:26px;top:18px" width="50" height="48" viewBox="0 0 50 48" fill="none" stroke="#1b3aa6" stroke-width="2">
      <path d="M6 20a19 19 0 0 1 38 0z"/><line x1="25" y1="20" x2="25" y2="38"/><path d="M25 1v2"/>
      <path d="M2 38h46M4 44h42"/><path d="M6 38v8M44 38v8"/><path d="M30 38l14-12"/>
    </svg>
    <h2 style="left:99px;top:16px">DECKS/PATIOS</h2>
    <p class="intro" style="left:99px;top:46px;width:336px">An outdoor space is a great addition to any residential property. When you decide to build a patio or deck, you'll be able to experience a variety of benefits. Your outdoor area will increase your:</p>
    <ul style="left:99px;top:122px;line-height:15px">
      <li style="margin-bottom:3px">Property value</li>
      <li style="margin-bottom:3px">Curb appeal</li>
      <li>Functional living<br>space</li>
    </ul>
    <div class="photo" role="img" aria-label="Screened porch with wood ceiling, ceiling fan and dining set overlooking trees"
      style="left:260px;top:116px;width:207px;height:180px;background:linear-gradient(180deg,#a9774a 0%,#cfd8d2 30%,#6f9a55 60%,#6b4630 100%)"></div>
  </section>

  <footer class="footer">
    <div class="contact" style="left:38px">
      <svg width="16" height="16" viewBox="0 0 16 16" fill="none" stroke="#fff" stroke-width="1.2"><circle cx="8" cy="8" r="7"/><ellipse cx="8" cy="8" rx="3" ry="7"/><path d="M1 8h14M2.5 4.5h11M2.5 11.5h11"/></svg>
      www.larkmoorhomeworks.com
    </div>
    <div class="contact" style="left:305px">
      <svg width="16" height="12" viewBox="0 0 16 12" fill="none" stroke="#fff" stroke-width="1.2"><rect x=".6" y=".6" width="14.8" height="10.8"/><path d="M.6.6 8 7l7.4-6.4"/></svg>
      hello@larkmoorhomeworks.com
    </div>
  </footer>

</div>
</body>
</html>
```